Kestal-Materials. Limestone; improving the world

New Limestone company and need logo design.
Limestone offsets carbon mitigation industries restore and replenish soil fertilities in the Prairies, the breadbasket of the world. At the same time, Limestone is proving a critical emergent component of carbon capture sequestration technology will therefore play a critical role in the development of the western Canadian energy industries
Our limestone resources are situated in the foothills of the Canadian Rockies well-positioned above the sprawling fields of the vast peace district.
Agriculture and oli sites
Kestal Materials
3 page

```html
<!DOCTYPE html>
<html lang="en">
<head>
<meta charset="utf-8">
<title>Kestal Materials</title>
<link href="https://fonts.googleapis.com/css2?family=Oswald:wght@500;600;700&family=Montserrat:wght@400;500;600;700&display=swap" rel="stylesheet">
<style>
:root{
  --green:#238a1e;
  --blue:#3a93c4;
  --ink:#1b1b1b;
  --body:#6c6c6c;
  --navy:#13273a;
  --white:#fff;
}
*{box-sizing:border-box;margin:0;padding:0}
html,body{width:1200px;height:2754px;overflow:hidden;background:var(--white);font-family:'Montserrat',sans-serif}
.page{position:relative;width:1200px;height:2754px}
.abs{position:absolute}
.btn{position:absolute;display:flex;align-items:center;justify-content:center;background:var(--green);color:var(--white);font-weight:700;font-size:15px;border-radius:32px;text-transform:uppercase;white-space:nowrap}
.display{font-family:'Oswald',sans-serif;font-weight:600;text-transform:uppercase;letter-spacing:-.5px}

.hero{left:0;top:0;width:1200px;height:636px;background:radial-gradient(ellipse at 55% 45%,#5f7a3a 0%,#3d5a34 28%,#1d4a6e 55%,#0d2f52 100%)}
.hero::before{content:"";position:absolute;inset:0;background:linear-gradient(#0b1a14 0%,rgba(11,26,20,.4) 18%,rgba(0,0,0,0) 40%)}
.logo{left:143px;top:36px;font-family:'Oswald',sans-serif;font-weight:600;font-size:36px;color:var(--white);letter-spacing:-.5px;line-height:44px}
.nav{left:488px;top:51px;display:flex;gap:26px;font-size:11px;color:var(--white);white-space:nowrap}
.nav .active{position:relative}
.nav .active::after{content:"";position:absolute;left:-4px;right:-4px;top:19px;height:3px;background:var(--blue);border-radius:2px}
.portal{left:901px;top:37px;width:154px;height:43px;font-size:11.5px}
.hero-title{left:0;width:1200px;top:222px;text-align:center;font-size:78px;color:var(--white);line-height:1}
.hero-sub{left:0;width:1200px;top:331px;text-align:center;font-size:25px;font-weight:700;color:var(--white)}
.hero-btn{left:501px;top:405px;width:199px;height:65px;font-size:16px}
.dots{left:555px;top:563px;display:flex;gap:10px}
.dots span{width:9px;height:9px;border-radius:50%;background:var(--white)}
.dots .on{background:var(--green)}

.about-title{left:145px;top:700px;font-size:46px;color:var(--ink)}
.about-text{left:145px;top:781px;width:410px;font-size:14.5px;line-height:26.4px;color:var(--body)}
.about-btn{left:145px;top:1022px;width:167px;height:55px}
.about-media{left:582px;top:705px;width:474px;height:372px;background:linear-gradient(#2f5f9c 0%,#7fa6cd 45%,#b9b6ac 65%,#8d8c86 100%)}
.play{left:788px;top:875px}

.products{left:0;top:1162px;width:1200px;height:609px;background:radial-gradient(ellipse at 35% 50%,#d8ccb0 0%,#b9aa8c 45%,#8a7a62 100%)}
.products-circle{left:654px;top:1265px;width:402px;height:402px;border-radius:50%;background:rgba(58,147,196,.93)}
.products-title{left:654px;width:402px;top:1325px;text-align:center;font-size:46px;color:var(--white)}
.products-text{left:705px;width:300px;top:1396px;text-align:center;font-size:14.5px;line-height:25px;color:var(--white)}
.products-btn{left:771px;top:1545px;width:168px;height:55px}

.res-title{left:0;width:1200px;top:1862px;text-align:center;font-size:48px;color:var(--ink)}
.card{position:absolute;top:1969px;width:277px;height:353px;border:2px solid #d7d7d7;background:var(--white)}
.card.raised{box-shadow:0 4px 14px rgba(0,0,0,.18)}
.card-img{position:absolute;left:10px;top:9px;width:254px;height:155px}
.date{position:absolute;left:20px;top:189px;width:50px;height:47px;background:var(--blue);color:var(--white);text-align:center;font-weight:600;line-height:1}
.date b{display:block;font-size:20px;padding-top:5px}
.date small{font-size:14px}
.card-head{position:absolute;left:80px;top:188px;font-size:15px;font-weight:700;color:var(--ink);line-height:23px;white-space:nowrap}
.card-text{position:absolute;left:21px;top:251px;width:245px;font-size:11.3px;line-height:19px;color:var(--body);letter-spacing:-.1px}
.card-link{position:absolute;left:20px;top:318px;font-size:13.5px;font-weight:700;color:var(--green)}
.arrow{position:absolute;top:2122px}

.footer{left:0;top:2414px;width:1200px;height:340px;background:linear-gradient(#16314a,#13283c)}
.contact{position:absolute;top:2455px;display:flex;align-items:center;gap:12px;color:var(--white);font-size:14.5px;line-height:21px;white-space:nowrap}
.ico{width:40px;height:40px;border-radius:50%;display:flex;align-items:center;justify-content:center;flex:none}
.ico.w{background:var(--white)}
.ico.b{background:var(--blue)}
.rule{left:0;top:2535px;width:1200px;height:1px;background:rgba(255,255,255,.08)}
.fnav{left:0;width:1200px;top:2578px;display:flex;justify-content:center;gap:32px;font-size:19px;font-weight:700;color:var(--white)}
.copy{left:0;width:1200px;top:2636px;text-align:center;font-size:13px;color:var(--white)}
.social{left:551px;top:2692px;display:flex;gap:8px}
.social span{width:26px;height:26px;border-radius:50%}
</style>
</head>
<body>
<div class="page">

  <section class="abs hero" role="img" aria-label="Aerial photo of a forested limestone island in deep blue sea"></section>
  <div class="abs logo">Kestal Materials</div>
  <nav class="abs nav">
    <span class="active">HOME</span><span>PRODUCTS</span><span>MARKETS</span><span>ABOUT US</span><span>LOCATIONS</span>
  </nav>
  <div class="btn portal">Customer Portal</div>
  <h1 class="abs hero-title display">Kestal Materials</h1>
  <p class="abs hero-sub">We are a New Limestone company</p>
  <div class="btn hero-btn">Get Started</div>
  <div class="abs dots"><span></span><span></span><span class="on"></span><span></span><span></span></div>

  <h2 class="abs about-title display">Who We Are</h2>
  <p class="abs about-text">Lorem ipsum dolor sit amensectetur adipiscing elied do eiusmod tempor incididunt ut labore et dolore magna aliquauis ipsum suspendisse ultrices gravidisus ommodo viverra maecenas accumsan lacus vel facilisis.orem ipsum dolor sit amensectetur adipiscing elied do eiusmod tempor incididunt ut labore et dolore magna aliquauis ipsum suspendisse ultricesavidisus commodo viverra maeumsan lacus vel facilisis.</p>
  <div class="btn about-btn">Read More</div>
  <div class="abs about-media" role="img" aria-label="Conveyor belts dropping crushed limestone onto a stockpile under blue sky"></div>
  <svg class="abs play" width="64" height="64" viewBox="0 0 64 64">
    <circle cx="32" cy="32" r="29" fill="none" stroke="#fff" stroke-width="4"/>
    <path d="M26 21 L44 32 L26 43 Z" fill="#fff"/>
  </svg>

  <section class="abs products" role="img" aria-label="Close-up of crushed white limestone rocks"></section>
  <div class="abs products-circle"></div>
  <h2 class="abs products-title display">Products</h2>
  <p class="abs products-text">Lorem ipsum dolor sit amet, consectetur adipiscing elit, sed do eiusmod tempor incididunt ut labore et dolore magna aliquacommodo viverra maecenas accumsan lacus</p>
  <div class="btn products-btn">Read More</div>

  <h2 class="abs res-title display">Latest Resources</h2>

  <svg class="arrow" style="left:55px" width="36" height="66" viewBox="0 0 36 66"><path d="M34 1 L2 33 L34 65" fill="none" stroke="#9a9a9a" stroke-width="1.5"/></svg>
  <svg class="arrow" style="left:1110px" width="36" height="66" viewBox="0 0 36 66"><path d="M2 1 L34 33 L2 65" fill="none" stroke="#9a9a9a" stroke-width="1.5"/></svg>

  <article class="card" style="left:156px">
    <div class="card-img" role="img" aria-label="Pile of white limestone gravel" style="background:linear-gradient(135deg,#d9d6cf,#a8a49b)"></div>
    <div class="date"><b>02</b><small>JAN</small></div>
    <h3 class="card-head">Pellentesque faucibus<br>Ut accumsan ultric</h3>
    <p class="card-text">Duis quam Nam eget lacus Aliquam erat volutpat Quisque dignissim congue leovel lacus vitae felis vestibulum</p>
    <span class="card-link">READ MORE</span>
  </article>
  <article class="card raised" style="left:462px">
    <div class="card-img" role="img" aria-label="Quarry wall with broken limestone debris" style="background:linear-gradient(#b2aea6,#8b867d)"></div>
    <div class="date"><b>02</b><small>JAN</small></div>
    <h3 class="card-head">Pellentesque faucibus<br>Ut accumsan ultric</h3>
    <p class="card-text">Duis quam Nam eget lacus Aliquam erat volutpat Quisque dignissim congue leovel lacus vitae felis vestibulum</p>
    <span class="card-link">READ MORE</span>
  </article>
  <article class="card" style="left:768px">
    <div class="card-img" role="img" aria-label="Open limestone quarry under a cloudy sky" style="background:linear-gradient(#3c4e63 0%,#8d8070 25%,#d4ccbf 60%,#b1a898 100%)"></div>
    <div class="date"><b>02</b><small>JAN</small></div>
    <h3 class="card-head">Pellentesque faucibus<br>Ut accumsan ultric</h3>
    <p class="card-text">Duis quam Nam eget lacus Aliquam erat volutpat Quisque dignissim congue leovel lacus vitae felis vestibulum</p>
    <span class="card-link">READ MORE</span>
  </article>

  <footer class="abs footer"></footer>
  <div class="contact" style="left:220px">
    <span class="ico w"><svg width="12" height="14" viewBox="0 0 12 14"><path d="M6 0a5 5 0 0 0-5 5c0 4 5 9 5 9s5-5 5-9a5 5 0 0 0-5-5zm0 7a2 2 0 1 1 0-4 2 2 0 0 1 0 4z" fill="#13273a"/></svg></span>
    <span>122.Lorem ipsum dolor siamet<br>consectetuipiscing elit.</span>
  </div>
  <div class="contact" style="left:519px">
    <span class="ico b"><svg width="13" height="13" viewBox="0 0 24 24"><path d="M6.6 10.8a15 15 0 0 0 6.6 6.6l2.2-2.2a1 1 0 0 1 1-.25 11.4 11.4 0 0 0 3.6.57 1 1 0 0 1 1 1V20a1 1 0 0 1-1 1A17 17 0 0 1 3 4a1 1 0 0 1 1-1h3.5a1 1 0 0 1 1 1c0 1.25.2 2.45.57 3.57a1 1 0 0 1-.25 1z" fill="#fff"/></svg></span>
    <span>1 888 888 8888</span>
  </div>
  <div class="contact" style="left:717px">
    <span class="ico w"><svg width="13" height="10" viewBox="0 0 13 10"><rect width="13" height="10" rx="1" fill="#13273a"/><path d="M0.5 1 L6.5 5.5 L12.5 1" fill="none" stroke="#fff" stroke-width="1.2"/></svg></span>
    <span>info@kestalmaterials.com</span>
  </div>
  <div class="abs rule"></div>
  <nav class="abs fnav">
    <span>HOME</span><span>/</span><span>PRODUCTS</span><span>/</span><span>MARKETS</span><span>/</span><span>ABOUT US</span><span>/</span><span>LOCATIONS</span>
  </nav>
  <p class="abs copy">Copyright 2021 Kestal Materials.All Rights Reserved &nbsp;|&nbsp; Privacy Policy</p>
  <div class="abs social">
    <span style="background:#2f5fd0"></span>
    <span style="background:#27a6de"></span>
    <span style="background:#e0161f"></span>
  </div>

</div>
</body>
</html>
```